Healthcare website

We want to replace our website using joomla as the CMS. We want it to be device agnostic (gantry etc). Our business is health care our clients are people with high level spinal cord injuries ( quadriplegia / tetraplegia etc ). The site is a marketing tool primarily to potential clients and a portal for existing staff to access forms etc. It will showcase our key staff and our capability. It will also be where any new recruits apply to work with us. It must allow us to integrate our social media initiatives also. The final design must convey sophistication, high quality care and be warm and welcoming.

current web site is www.tendralwick.com.au
Updates

I have made small change to the brief in that i have removed the prefered color and indicated it would be nice to see some images that symbolize change / transformation like butterflies etc. thank you

Target Market(s)

Our business is health care our clients are people with high level spinal cord injuries ( quadriplegia / tetraplegia etc ).

Industry/Entity Type

Marketing

Colors

Designer to choose colors to be used in the design.

Requirements
Must have
• The site is a marketing tool primarily to potential clients and a portal for existing staff to access forms etc. It will showcase our key staff and our capability. It will also be where any new recruits apply to work with us. It must allow us to integrate our social media initiatives also. The final design must convey sophistication, high quality care and be warm and welcoming.
Nice to have
• Would be nice to incorporate images that symbolize change and new transformations - butterflies etc.

```html
<!DOCTYPE html>
<html lang="en">
<head>
<meta charset="utf-8">
<title>Tendral Care</title>
<link rel="stylesheet" href="https://fonts.googleapis.com/css2?family=Open+Sans:wght@300;400;600&family=Bitter:wght@400&family=Roboto+Condensed:wght@400&display=swap">
<style>
:root{
  --blue:#2f74bb;
  --blue-dark:#1f5c9e;
  --ink:#222;
  --muted:#444;
  --line:#d6d6d6;
  --panel:#f6f6f6;
  --footer-text:#e6effa;
}
*{box-sizing:border-box;margin:0;padding:0}
html,body{width:798px;height:1200px;overflow:hidden;background:#fff}
body{position:relative;font-family:"Open Sans",Arial,sans-serif;color:var(--ink);font-size:8.4px;line-height:1.4}
.abs{position:absolute}
.topline{left:0;top:0;width:798px;height:2px;background:#cfcfcf}
.brand{left:102px;top:26px;display:flex;align-items:center;gap:6px;font-size:15px;font-weight:600;color:var(--blue)}
.brand-dot{width:16px;height:16px;border-radius:50%;background:var(--blue)}
.nav{left:229px;top:19px;display:flex;height:26px;align-items:center;white-space:nowrap}
.nav a{font-size:9px;color:var(--ink);text-decoration:none;padding:0 11px;border-right:1px solid var(--line);line-height:26px}
.nav a:last-child{border-right:none}
.search{left:597px;top:23px;width:98px;height:19px;border:1px solid #c8c8c8;font-size:7.5px;color:#666;padding:4px 7px}
.search svg{position:absolute;right:5px;top:4px}
.hero{left:0;top:64px;width:798px;height:292px;background:linear-gradient(135deg,#b7a48e 0%,#8a8f88 35%,#c9c1b0 60%,#7c7f83 100%)}
.arrow{width:30px;height:30px;background:#111;top:196px}
.arrow svg{display:block}
.caption{left:116px;top:200px;width:397px;height:23px;background:rgba(40,40,40,.7);color:#eee;font-size:11px;font-weight:300;padding:3px 5px;line-height:17px;white-space:nowrap;overflow:hidden}
.dots{left:372px;top:336px;display:flex;gap:2px}
.dots span{width:7px;height:7px;border-radius:50%;background:#111}
.dots span.on{background:var(--blue)}
h2{font-family:"Bitter",Georgia,serif;font-weight:400;color:var(--blue);font-size:10.6px}
.welcome{left:102px;top:374px;width:345px}
.welcome p{margin-top:4px;margin-bottom:6px}
.feature-box{left:102px;top:453px;width:344px;height:139px;background:var(--panel);padding:11px 0 0 16px}
ul.ticks{list-style:none}
ul.ticks li{position:relative;padding-left:13px;margin-bottom:10px}
ul.ticks li::before{content:"";position:absolute;left:2px;top:3px;border-left:5px solid #333;border-top:3px solid transparent;border-bottom:3px solid transparent}
.support-title{left:102px;top:611px}
.support{left:116px;top:637px;width:335px}
.support li{margin-bottom:9px}
.card{left:470px;width:226px}
.card .photo{width:225px;height:62px;margin-top:3px}
.card p{margin-top:6px;font-size:8.2px}
.more{display:block;margin-left:auto;margin-top:0;width:50px;background:var(--blue);color:#fff;font-size:7.4px;padding:1px 3px;text-align:right}
.news{left:101px;top:763px;width:595px;height:182px;border:1px solid var(--blue)}
.news h2{text-align:center;font-size:13px;margin-top:10px}
.news-nav{position:absolute;left:278px;top:33px;display:flex;gap:3px}
.news-nav span{width:14px;height:14px;background:var(--blue);display:block}
.news-cols{position:absolute;top:70px;left:16px;display:flex}
.news-item{position:relative;width:200px;padding:0 45px 0 15px;border-right:1px solid var(--line)}
.news-item:last-child{border-right:none}
.news-item::before{content:"";position:absolute;left:2px;top:3px;width:5px;height:5px;border-right:1px solid #333;border-bottom:1px solid #333;transform:rotate(-45deg)}
.news-item h3{font-family:"Roboto Condensed",Arial,sans-serif;font-weight:400;font-size:9px;line-height:1.35;color:#111}
.news-item p{margin-top:4px;font-size:8.2px}
.news-item a{display:block;margin-top:6px;color:var(--blue);font-weight:600;text-decoration:none;font-size:8px}
.footer{left:0;top:960px;width:798px;height:240px;background:var(--blue)}
.footer-about{left:102px;top:974px;width:280px;font-size:7.4px;line-height:1.83;color:var(--footer-text)}
.badges{left:102px;top:1048px;display:flex;gap:10px;align-items:center}
.badges span{background:rgba(255,255,255,.85);display:block}
.rule{left:102px;width:278px;height:1px;background:rgba(255,255,255,.35)}
.follow{left:102px;top:1106px;font-size:7.4px;color:var(--footer-text)}
.social{left:102px;top:1121px;display:flex;gap:4px}
.social span{width:17px;height:17px;border-radius:50%;background:#fff;display:block}
.office{left:424px;top:974px;font-size:7.4px;line-height:1.75;color:var(--footer-text)}
.office strong{font-weight:600;color:#fff}
.map{left:424px;top:1005px;width:272px;height:147px;background:linear-gradient(160deg,#e8e2cf,#d9d4c2 50%,#e7d9a8);border:2px solid #e3edf8}
.bottomrule{left:102px;top:1170px;width:594px;height:1px;background:rgba(255,255,255,.3)}
.legal{left:102px;top:1177px;font-size:7.4px;color:var(--footer-text)}
</style>
</head>
<body>
<div class="abs topline"></div>
<header>
  <div class="abs brand"><span class="brand-dot"></span>Tendral Care</div>
  <nav class="abs nav">
    <a href="#">HOME</a><a href="#">ABOUT US</a><a href="#">OUR SERVICES</a><a href="#">RESOURCES</a><a href="#">CONTACT US</a>
  </nav>
  <div class="abs search">Search
    <svg width="10" height="10" viewBox="0 0 10 10"><circle cx="4" cy="4" r="3" fill="none" stroke="#777" stroke-width="1.2"/><line x1="6.2" y1="6.2" x2="9" y2="9" stroke="#777" stroke-width="1.4"/></svg>
  </div>
</header>

<section>
  <div class="abs hero" role="img" aria-label="Photo of a carer and a client smiling outside a suburban home"></div>
  <div class="abs arrow" style="left:86px"><svg width="30" height="30"><polyline points="18,8 11,15 18,22" fill="none" stroke="#fff" stroke-width="1.6"/></svg></div>
  <div class="abs arrow" style="left:681px"><svg width="30" height="30"><polyline points="12,8 19,15 12,22" fill="none" stroke="#fff" stroke-width="1.6"/></svg></div>
  <div class="abs caption">Tendral Care has built its service around the needs of each and every client</div>
  <div class="abs dots"><span></span><span></span><span class="on"></span><span></span><span></span></div>
</section>

<main>
  <div class="abs welcome">
    <h2>Welcome to Tendral Care</h2>
    <p>Tendral Care is a small team of care professionals committed to providing quality one-to-one care with heart.</p>
    <p>Tendral Care has built its service around the needs of each and every client. We listen to and consult with our clients, their families, Care Teams and the wider care community.</p>
  </div>
  <div class="abs feature-box">
    <ul class="ticks">
      <li>Professionally supported one-to-one home based care</li>
      <li>Expert specialist care for clients with SCI &amp; ABI</li>
      <li>Assistance with daily living tasks community and recreation access</li>
      <li>Tendral Care is available 24 hours seven days per week.</li>
      <li>Tendral Care is Road Injury Commission (RIC), State Workplace Authority (SWA) and Department of Community Care (DCC) approved.</li>
    </ul>
  </div>
  <h2 class="abs support-title">You can rely on professional support by the Team at Tendral Care</h2>
  <ul class="abs ticks support">
    <li>All our Care Managers are highly experienced professionals.</li>
    <li>Our Care Teams are highly experienced and knowledgeable in SCI &amp; ABI</li>
    <li>Our Care Teams also understands the broader medical issues of your disability.</li>
    <li>Every member of your Care Team will receive our unique industry specific training in SCI &amp; ABI as well as the use of your specialised equipment</li>
  </ul>

  <article class="abs card" style="top:375px">
    <h2>Attendant Care - Personal Care</h2>
    <div class="photo" role="img" aria-label="Photo of a nurse attending to a client at home" style="background:linear-gradient(90deg,#9fc3c4,#e8ddd0 55%,#c9a896)"></div>
    <p>Tendral Care has built its services around the needs of each and every client</p>
    <span class="more">&rsaquo; Read More</span>
  </article>
  <article class="abs card" style="top:503px">
    <h2>Spinal Care - SCI</h2>
    <div class="photo" role="img" aria-label="Photo of two smiling care workers" style="background:linear-gradient(90deg,#dfe3e6,#c9b8a8 45%,#8b8f96 80%,#e4e6e8)"></div>
    <p>Tendral Care has developed a highly focused specialisation in Spinal Cord Injury.</p>
    <span class="more">&rsaquo; Read More</span>
  </article>
  <article class="abs card" style="top:631px">
    <h2>Refer a client</h2>
    <div class="photo" role="img" aria-label="Photo of friends sharing a recommendation" style="background:linear-gradient(90deg,#b0826a,#e1bfa6 50%,#a97a62)"></div>
    <p>At Tendral Care our clients care is our 1st priority. Our measure of success is their satisfaction.</p>
    <span class="more">&rsaquo; Read More</span>
  </article>

  <section class="abs news">
    <h2>Disability News</h2>
    <div class="news-nav">
      <span><svg width="14" height="14"><polygon points="9,3 4,7 9,11" fill="#fff"/></svg></span>
      <span><svg width="14" height="14"><polygon points="5,3 10,7 5,11" fill="#fff"/></svg></span>
    </div>
    <div class="news-cols">
      <div class="news-item">
        <h3>New Methods Show Promise for Rehabilitating Paralyzed Patients With Spinal Cord Injury</h3>
        <p>A paraplegic wearing a robot-like exoskeleton took the first kick of the World</p>
        <a href="#">Read More &gt;&gt;</a>
      </div>
      <div class="news-item">
        <h3>Stem-cell advances may quell ethics debate</h3>
        <p>Martin Hale says he’s glad the stem cells that healed him came from “a guy who was 50 years old” and not a human embryo.</p>
        <a href="#">Read More &gt;&gt;</a>
      </div>
      <div class="news-item">
        <h3>Wheelchair rugby a family affair for mom and son</h3>
        <p>Dana Prell choked back tears as her shy, 11-year-old son, Owen Prell, guided his wheelchair out to centre court Thursday -</p>
        <a href="#">Read More &gt;&gt;</a>
      </div>
    </div>
  </section>
</main>

<footer>
  <div class="abs footer"></div>
  <p class="abs footer-about">Tendral Care is proud to be an approved provider for Road Injury Commission (RIC), State Workplace Authority (SWA), Department of Community Care (DCC) and maintain associations and cooperative relationships with a variety of private and governmental organisations in its efforts to bring the finest, most up-to-date care for its clients.</p>
  <div class="abs badges">
    <span style="width:14px;height:22px"></span>
    <span style="width:14px;height:22px"></span>
    <span style="width:14px;height:16px;border-radius:50%"></span>
    <span style="width:58px;height:16px"></span>
    <span style="width:30px;height:22px"></span>
    <span style="width:26px;height:12px"></span>
    <span style="width:30px;height:14px"></span>
  </div>
  <div class="abs rule" style="top:1092px"></div>
  <div class="abs follow">Follow Us On</div>
  <div class="abs social"><span></span><span></span><span></span><span></span></div>
  <div class="abs office"><strong>Tendral Care - Ashbury</strong><br>42 - 44 Linden Grove Rd, Ashbury Vale, 3100 Ph : (03) 5550 1742</div>
  <div class="abs map" role="img" aria-label="Street map showing the office location"></div>
  <div class="abs bottomrule"></div>
  <div class="abs legal">Privacy &nbsp;| &nbsp;Terms of Service &nbsp;| &nbsp;© 2004 - 2014 Tendral Care Pty Ltd</div>
</footer>
</body>
</html>
```